Velvet Lantern rebranding my business with a new business card

I have my new logo and now I need a refresher on my business cards. I really want something fun and fresh. I like black background or anything to make the color pop.
Logo
Name: Velvet Lantern
Contact Info as stated below:
Mira Pellow
555-013-4762
Logo
Name: Velvet Lantern
Mira Pellow
555-013-4762
fb.me/VelvetLanternbyMira
Instagram: @VelvetLanternbyMira

Industry/Entity Type

Business

Contact Information for Business Card

double-sided. Logo on one side. Contact info on the other.

Requirements
Must have
• Logo
• Name: Velvet Lantern
• Contact Info as stated below:
• Mira Pellow
• 555-013-4762
• fb.me/VelvetLanternbyMira
• fb.me/VelvetLanternbyMira

```html
<!DOCTYPE html>
<html lang="en">
<head>
<meta charset="utf-8">
<title>Velvet Lantern – Business Card</title>
<link rel="stylesheet" href="https://fonts.googleapis.com/css2?family=Roboto:wght@400;500;700&family=Roboto+Condensed:wght@700&display=swap">
<style>
  :root {
    --backdrop: #ece7e3;
    --card-pink: #f0a6b4;
    --band-pink: #f2a9b7;
    --ink-black: #050505;
    --paper-white: #f4f4f4;
    --url-grey: #6e5c61;
    --logo-pink: #e98aa0;
    --logo-tone-a: #f4a3c0;
    --logo-tone-b: #7cc9c3;
    --text-white: #ffffff;
  }
  * { margin: 0; padding: 0; box-sizing: border-box; }
  html, body { width: 1200px; height: 960px; overflow: hidden; }
  body {
    background: var(--backdrop);
    font-family: "Roboto", Arial, sans-serif;
    position: relative;
  }
  .card {
    position: absolute;
    border-radius: 20px;
    overflow: hidden;
    box-shadow: 0 6px 14px rgba(0,0,0,0.25);
  }
  /* Front: logo side */
  .card-front {
    left: 320px; top: 100px; width: 606px; height: 340px;
    background: var(--card-pink);
  }
  .front-logo {
    position: absolute; left: 198px; top: 70px; width: 210px; height: 200px;
    display: flex; align-items: center; justify-content: center;
  }
  .logo-art {
    position: absolute; inset: 0;
    border-radius: 50%;
    background: radial-gradient(circle at 50% 40%, var(--logo-tone-a) 0%, rgba(244,163,192,0.35) 55%, rgba(124,201,195,0) 75%);
  }
  .brand-name {
    position: relative;
    font-family: "Roboto", Arial, sans-serif;
    font-weight: 700;
    font-size: 26px;
    line-height: 1.1;
    color: #3b2a2e;
    text-align: center;
    letter-spacing: 1px;
  }
  .front-url {
    position: absolute; left: 0; right: 0; top: 298px;
    text-align: center;
    font-size: 14px;
    letter-spacing: 5.2px;
    color: var(--url-grey);
  }
  /* Back: contact side */
  .card-back {
    left: 322px; top: 493px; width: 596px; height: 342px;
    background: var(--ink-black);
    border-radius: 18px;
  }
  .card-back svg.swoosh { position: absolute; inset: 0; }
  .holder-name {
    position: absolute; left: 35px; top: 38px;
    font-family: "Roboto Condensed", Arial, sans-serif;
    font-weight: 700; font-size: 21px;
    color: var(--text-white);
    letter-spacing: 0.2px;
  }
  .contact-list {
    position: absolute; left: 35px; top: 250px;
    list-style: none;
  }
  .contact-list li {
    display: flex; align-items: center;
    height: 19.5px;
    font-size: 14.5px;
    color: var(--text-white);
  }
  .contact-icon { width: 13px; height: 13px; margin-right: 16px; flex: none; }
  .badge-logo {
    position: absolute; left: 312px; top: 42px; width: 206px; height: 206px;
    display: flex; align-items: center; justify-content: center;
  }
  .badge-logo .brand-name { font-size: 22px; color: #3b2a2e; }
  .badge-logo .logo-art { inset: 26px; }
</style>
</head>
<body>

  <section class="card card-front" aria-label="Card front">
    <div class="front-logo">
      <div class="logo-art" role="img" aria-label="Brand illustration area"></div>
      <div class="brand-name">Velvet<br>Lantern</div>
    </div>
    <p class="front-url">www.velvetlantern.com</p>
  </section>

  <section class="card card-back" aria-label="Card back">
    <svg class="swoosh" width="596" height="342" viewBox="0 0 596 342" aria-hidden="true">
      <path d="M365 0 C262 12 218 100 226 182 C234 262 330 312 492 342 L596 342 L596 0 Z" fill="var(--band-pink)"/>
      <path d="M470 0 C330 8 248 96 250 182 C252 262 336 312 508 342 L596 342 L596 0 Z" fill="var(--ink-black)"/>
      <path d="M500 0 C350 14 258 100 260 184 C262 262 344 312 515 342 L596 342 L596 0 Z" fill="var(--paper-white)" stroke="#ffffff" stroke-width="2"/>
      <circle cx="415" cy="145" r="103" fill="#ffffff" stroke="#111" stroke-width="2"/>
      <circle cx="415" cy="145" r="96" fill="none" stroke="var(--logo-pink)" stroke-width="1.5"/>
      <circle cx="415" cy="145" r="92" fill="none" stroke="var(--logo-pink)" stroke-width="1"/>
    </svg>

    <div class="badge-logo">
      <div class="logo-art" role="img" aria-label="Brand illustration area"></div>
      <div class="brand-name">Velvet<br>Lantern</div>
    </div>

    <h1 class="holder-name">MIRA PELLOW</h1>

    <ul class="contact-list">
      <li>
        <svg class="contact-icon" viewBox="0 0 24 24" aria-hidden="true"><path fill="#fff" d="M6.6 10.8a15.1 15.1 0 0 0 6.6 6.6l2.2-2.2c.3-.3.7-.4 1-.2 1.1.4 2.3.6 3.6.6.6 0 1 .4 1 1V20c0 .6-.4 1-1 1C10.6 21 3 13.4 3 4c0-.6.4-1 1-1h3.5c.6 0 1 .4 1 1 0 1.3.2 2.5.6 3.6.1.3 0 .7-.2 1z"/></svg>
        555-013-4762
      </li>
      <li>
        <svg class="contact-icon" viewBox="0 0 24 24" aria-hidden="true"><circle cx="12" cy="12" r="10" fill="none" stroke="#fff" stroke-width="2.5"/><path d="M2 12h20M12 2c3 3 3 17 0 20M12 2c-3 3-3 17 0 20" fill="none" stroke="#fff" stroke-width="2"/></svg>
        www.velvetlantern.com
      </li>
      <li>
        <svg class="contact-icon" viewBox="0 0 24 24" aria-hidden="true"><rect x="2" y="2" width="20" height="20" rx="2" fill="#fff"/></svg>
        fb.me/VelvetLanternbyMira
      </li>
    </ul>
  </section>

</body>
</html>
```